Website for software company "velora"

We need a website for our software company/startup named "velora". We are developing several products (currently 3 standard-software products) which are all in different sectors, but all our products are available for Laptops/PC/Mobile Phones/Tablets, ... We do also create custom software and support our customers with consulting to optimize their processes.
We already have a Logo which you can find in the attached files.
We are a young team of 4 members (two founders and 2 employees).

To get an idea of our products -> the first one is a planning software for healthcare organizations (eg. BlueHaven, firebrigade, pharmacy), the second one is a booking software for sport clubs and the third one is a competition software for sports hunting. You see very diverse. Include or ignore this info of our products as you like.

The design has to be a bootstrap 4 (or higher) design. We have licenced FontAwesome as iconset. Responsive design should come without saying.

• Starting page, product pages, news section, contact, team, services

```html
<!DOCTYPE html>
<html lang="en">
<head>
<meta charset="utf-8">
<title>velora — Software that optimizes your processes</title>
<link rel="stylesheet" href="https://fonts.googleapis.com/css2?family=Montserrat:wght@300;400;500;600;700;800&display=swap">
<style>
  :root {
    --orange: #f47b20;
    --orange-deep: #ee5f1c;
    --ink: #232b36;
    --navy: #0f1a2e;
    --text: #3b4250;
    --muted: #7b8190;
    --soft: #eef0f4;
    --paper: #ffffff;
    --line: #d7dbe2;
    --peach: #fdeee2;
  }
  * { box-sizing: border-box; margin: 0; padding: 0; }
  html, body { width: 1200px; height: 4815px; overflow: hidden; }
  body { font-family: "Montserrat", sans-serif; color: var(--text); background: var(--paper); position: relative; }
  section, header, footer { position: absolute; left: 0; width: 1200px; overflow: hidden; }
  .abs { position: absolute; }

  .btn {
    position: absolute; display: flex; align-items: center; justify-content: center;
    height: 42px; border-radius: 21px; background: var(--orange); color: #fff;
    font-size: 13px; font-weight: 700; letter-spacing: .5px; text-transform: uppercase;
    box-shadow: 5px 0 0 rgba(244,123,32,.35);
  }
  .btn-small { height: 28px; border-radius: 14px; background: #fff; color: var(--orange); border: 1.5px solid var(--orange); font-size: 9px; box-shadow: none; }
  .btn-dark { background: var(--ink); box-shadow: 5px 0 0 rgba(35,43,54,.4); }

  .wordmark { font-weight: 800; letter-spacing: 1px; color: var(--ink); text-transform: uppercase; }
  .section-title { font-size: 37px; font-weight: 300; color: var(--ink); text-transform: uppercase; }
  .section-title b { font-weight: 700; }
  .product-title { font-size: 28px; font-weight: 700; color: var(--ink); text-transform: uppercase; }
  .product-title em { font-style: normal; color: var(--orange); }
  .copy { font-size: 14px; line-height: 26px; }
  .copy p + p { margin-top: 14px; }

  /* Header */
  .site-header { top: 0; height: 80px; background: #fff; }
  .site-header .wordmark { left: 127px; top: 18px; font-size: 38px; }
  .nav a { position: absolute; top: 30px; font-size: 12px; font-weight: 600; color: var(--ink); text-transform: uppercase; }
  .nav a.active { color: var(--orange); }
  .nav a.active::after { content: ""; position: absolute; left: -6px; right: -6px; bottom: -10px; height: 2px; background: var(--orange); }
  .nav .contact { left: 959px; top: 20px; width: 125px; height: 37px; border-radius: 19px; background: var(--orange); color: #fff; display: flex; align-items: center; justify-content: center; }

  /* Hero */
  .hero { top: 80px; height: 626px; background: var(--ink); }
  .hero h1 { position: absolute; left: 108px; top: 187px; font-size: 37px; line-height: 40px; font-weight: 300; color: #fff; text-transform: uppercase; }
  .hero h1 b { font-weight: 700; }
  .hero .lead { position: absolute; left: 112px; top: 312px; width: 400px; font-size: 14px; line-height: 21px; color: #e8eaee; }
  .device { position: absolute; border-radius: 10px; }

  /* About */
  .about { top: 706px; height: 615px; background: #fff; }
  .process-visual { position: absolute; left: 111px; top: 93px; width: 420px; height: 420px; border-radius: 50%; background: radial-gradient(circle, #fbd9bf 0%, var(--peach) 55%, #ffffff 100%); }
  .orbit-label { position: absolute; font-size: 11px; font-weight: 700; color: var(--ink); text-transform: uppercase; }

  /* Products */
  .products { top: 1321px; height: 604px; background: radial-gradient(ellipse at 70% 40%, #1c2a47 0%, var(--navy) 65%); }
  .products .section-title { color: #fff; text-align: center; width: 100%; top: 42px; position: absolute; }
  .underline { position: absolute; width: 72px; height: 3px; background: var(--orange); }

  /* Booking */
  .booking { top: 1925px; height: 538px; background: #fff; }
  /* Competition */
  .competition { top: 2463px; height: 542px; background: var(--soft); }

  /* Services */
  .services { top: 3005px; height: 587px; background: #fff; }
  .service { position: absolute; width: 260px; text-align: center; }
  .service h3 { font-size: 13px; font-weight: 700; color: var(--ink); text-transform: uppercase; margin-bottom: 12px; }
  .service p { font-size: 11px; line-height: 19px; color: var(--muted); }
  .service-icon { position: absolute; width: 92px; height: 92px; border-radius: 50%; }

  /* News */
  .news { top: 3592px; height: 553px; background: #f3f4f7; }
  .card { position: absolute; top: 131px; width: 297px; height: 356px; background: #fff; }
  .card .photo { height: 196px; }
  .card .body { padding: 18px 34px; }
  .card .date { font-size: 10px; font-weight: 700; color: var(--ink); }
  .card h4 { font-size: 13px; line-height: 19px; font-weight: 700; color: var(--ink); margin-top: 6px; }
  .card p { font-size: 10px; line-height: 17px; color: var(--muted); margin-top: 8px; }

  /* CTA */
  .cta { top: 4145px; height: 387px; background: linear-gradient(100deg, var(--orange) 0%, var(--orange-deep) 100%); text-align: center; color: #fff; }
  .cta h2 { position: absolute; top: 148px; width: 100%; font-size: 29px; font-weight: 700; text-transform: uppercase; }
  .cta h3 { position: absolute; top: 187px; width: 100%; font-size: 27px; font-weight: 300; text-transform: uppercase; }

  /* Footer */
  .site-footer { top: 4532px; height: 283px; background: var(--ink); color: #cfd3da; }
  .site-footer .wordmark { left: 160px; top: 64px; font-size: 42px; color: #fff; }
  .footer-col { position: absolute; top: 72px; padding-left: 42px; border-left: 3px solid var(--orange); height: 30px; }
  .footer-col h5 { font-size: 12px; font-weight: 700; color: #fff; text-transform: uppercase; line-height: 30px; }
  .footer-col ul { list-style: none; margin-top: 10px; }
  .footer-col li { font-size: 12px; line-height: 28px; color: #cfd3da; }
  .social { display: flex; gap: 8px; margin-top: 14px; }
  .social span { width: 28px; height: 28px; border-radius: 50%; background: #fff; display: block; }
  .social span:first-child { background: var(--orange); }
</style>
</head>
<body>

<header class="site-header">
  <div class="abs wordmark">velora</div>
  <nav class="nav">
    <a class="active" style="left:420px">Product</a>
    <a style="left:544px">Services</a>
    <a style="left:668px">News</a>
    <a style="left:766px">Team</a>
    <a style="left:863px">About</a>
    <a class="contact abs">Contact</a>
  </nav>
</header>

<section class="hero">
  <svg class="abs" style="left:0;top:0" width="1200" height="626" viewBox="0 0 1200 626">
    <polygon points="555,0 1200,0 1200,390" fill="#f47b20"/>
    <polygon points="700,0 1200,0 1200,250" fill="#f7924a" opacity=".55"/>
    <polygon points="850,626 1200,420 1200,626" fill="#f47b20"/>
  </svg>
  <h1>We help customer<br><b>to optimize their<br>processes</b></h1>
  <p class="lead">Lorem ipsum dolor sit amet, consectetur adipiscing elit, sed do eiusmod tempor incididunt.</p>
  <a class="btn" style="left:108px;top:383px;width:167px">Learn more</a>
  <div class="device" role="img" aria-label="Laptop showing the velora analytics dashboard" style="left:536px;top:107px;width:582px;height:364px;background:linear-gradient(180deg,#f4f6fa 0%,#e2e6ee 88%,#b9bec8 100%);border:10px solid #e9ecf1;border-bottom-width:18px"></div>
</section>

<section class="about">
  <div class="process-visual" role="img" aria-label="Illustration of the velora process cycle: optimize, support and develop"></div>
  <div class="orbit-label" style="left:290px;top:78px">Optimize</div>
  <div class="orbit-label" style="left:475px;top:365px">Support</div>
  <div class="orbit-label" style="left:187px;top:507px">Develop</div>

  <h2 class="abs section-title" style="left:620px;top:135px">About <b>velora</b></h2>
  <div class="abs copy" style="left:620px;top:218px;width:470px">
    <p>Lorem ipsum dolor sit amet, consectetur adipiscing elit, sed do eiusmod tempor incididunt ut labore et dolore magna aliqua. Ut enim ad minim veniam, quis nostrud</p>
    <p>exercitation ullamco laboris nisi ut aliquip ex ea commodo consequat. Duis aute irure dolor in reprehenderit in voluptate velit esse cillum dolore eu fugiat nulla pariatur.</p>
  </div>
  <a class="btn" style="left:615px;top:419px;width:160px">Learn more</a>
</section>

<section class="products">
  <h2 class="section-title">Our <b>Products</b></h2>
  <div class="underline" style="left:564px;top:93px"></div>
  <h3 class="abs product-title" style="left:137px;top:195px;color:#fff"><em>Planning</em> software</h3>
  <div class="abs copy" style="left:137px;top:245px;width:425px;color:#d9dde6">
    <p>Lorem ipsum dolor sit amet, consectetur adipiscing elit, sed do eiusmod tempor incididunt ut labore et dolore magna aliqua. Ut enim ad minim veniam, quis nostrud</p>
    <p>exercitation ullamco laboris nisi ut aliquip ex ea commodo consequat. Duis aute irure dolo</p>
  </div>
  <a class="btn" style="left:134px;top:414px;width:166px">Learn more</a>
  <div class="device" role="img" aria-label="Laptop showing the planning software dashboard" style="left:576px;top:169px;width:523px;height:291px;background:linear-gradient(180deg,#f4f7fc 0%,#dfe6f2 90%,#b7bcc6 100%);border:8px solid #e6e9ef;border-bottom-width:14px"></div>
</section>

<section class="booking">
  <svg class="abs" style="left:0;top:0" width="620" height="538" viewBox="0 0 620 538">
    <path d="M0,0 H500 C420,40 400,110 500,180 C580,240 560,420 470,470 C420,500 380,520 360,538 H0 Z" fill="#f47b20"/>
  </svg>
  <div class="device" role="img" aria-label="Phone showing booking software with outbound trip options" style="left:215px;top:45px;width:221px;height:428px;border-radius:22px;background:linear-gradient(180deg,#2f6fe0 0%,#2f6fe0 33%,#ffffff 34%,#ffffff 100%);border:6px solid #fff;box-shadow:0 10px 30px rgba(0,0,0,.15)"></div>
  <h3 class="abs product-title" style="left:635px;top:148px"><em>Booking</em> software</h3>
  <div class="abs copy" style="left:635px;top:198px;width:425px">
    <p>Lorem ipsum dolor sit amet, consectetur adipiscing elit, sed do eiusmod tempor incididunt ut labore et dolore magna aliqua. Ut enim ad minim veniam, quis nostrud</p>
    <p>exercitation ullamco laboris nisi ut aliquip ex ea commodo consequat. Duis aute irure dolo</p>
  </div>
  <a class="btn" style="left:632px;top:366px;width:166px">Learn more</a>
</section>

<section class="competition">
  <svg class="abs" style="left:0;top:0" width="1200" height="542" viewBox="0 0 1200 542">
    <polygon points="630,0 900,0 765,80" fill="#dfe2e8"/>
    <polygon points="1050,0 1200,0 1200,180" fill="#f6e3d6"/>
  </svg>
  <h3 class="abs product-title" style="left:137px;top:142px"><em>Competition</em> software</h3>
  <div class="abs copy" style="left:137px;top:192px;width:425px">
    <p>Lorem ipsum dolor sit amet, consectetur adipiscing elit, sed do eiusmod tempor incididunt ut labore et dolore magna aliqua. Ut enim ad minim veniam, quis nostrud</p>
    <p>exercitation ullamco laboris nisi ut aliquip ex ea commodo consequat. Duis aute irure dolo</p>
  </div>
  <a class="btn" style="left:134px;top:363px;width:166px">Learn more</a>
  <div class="device" role="img" aria-label="Tablet showing competition statistics and investments" style="left:598px;top:92px;width:467px;height:357px;border-radius:14px;background:linear-gradient(180deg,#ffffff 0%,#f1f3f7 100%);border:14px solid #1d222b"></div>
</section>

<section class="services">
  <h2 class="abs section-title" style="top:72px;width:100%;text-align:center">velora <b>Services</b></h2>
  <div class="abs wordmark" style="top:148px;width:100%;text-align:center;font-size:22px;color:var(--orange)">velora</div>
  <svg class="abs" style="left:0;top:0" width="1200" height="300" viewBox="0 0 1200 300">
    <path d="M295,257 V221 H903 V257 M603,185 V221" fill="none" stroke="#c9cdd5" stroke-width="2"/>
  </svg>
  <div class="service-icon" style="left:249px;top:257px;background:var(--ink);box-shadow:0 0 0 5px #fff,0 0 0 7px var(--ink)"></div>
  <div class="service-icon" style="left:565px;top:257px;background:var(--orange);box-shadow:0 0 0 5px #fff,0 0 0 7px var(--orange)"></div>
  <div class="service-icon" style="left:861px;top:257px;background:var(--ink);box-shadow:0 0 0 5px #fff,0 0 0 7px var(--ink)"></div>
  <div class="service" style="left:166px;top:372px"><h3>Custom software</h3><p>Lorem ipsum dolor sit amet, consectetur adipiscing elit, sed do eiusmod tempor incididunt ut labore et.</p></div>
  <div class="service" style="left:483px;top:372px"><h3>Customer support</h3><p>Lorem ipsum dolor sit amet, consectetur adipiscing elit, sed do eiusmod tempor incididunt ut labore et.</p></div>
  <div class="service" style="left:778px;top:372px"><h3>Optimize process</h3><p>Lorem ipsum dolor sit amet, consectetur adipiscing elit, sed do eiusmod tempor incididunt ut labore et.</p></div>
  <a class="btn" style="left:535px;top:500px;width:166px">Learn more</a>
</section>

<section class="news">
  <h2 class="abs section-title" style="left:127px;top:66px">Latest <b>News</b></h2>
  <article class="card" style="left:127px">
    <div class="photo" role="img" aria-label="Developer typing code at a laptop" style="background:linear-gradient(135deg,#2b3442,#6c7684)"></div>
    <div class="body"><div class="date">JAN 24, 2022</div><h4>Sed ut perspiciatis unde omnis iste natus error sit voluptatem</h4><p>Lorem ipsum dolor sit amet consectetur adipiscing elit, sed do eiusmod tempor</p></div>
    <a class="btn btn-small" style="left:34px;top:307px;width:110px">Learn more</a>
  </article>
  <article class="card" style="left:449px">
    <div class="photo" role="img" aria-label="Hands working at a desktop with charts on screen" style="background:linear-gradient(135deg,#e7eaee,#aab2bd)"></div>
    <div class="body"><div class="date">JAN 24, 2022</div><h4>Sed ut perspiciatis unde omnis iste natus error sit voluptatem</h4><p>Lorem ipsum dolor sit amet consectetur adipiscing elit, sed do eiusmod tempor</p></div>
    <a class="btn btn-small" style="left:34px;top:307px;width:110px">Learn more</a>
  </article>
  <article class="card" style="left:765px">
    <div class="photo" role="img" aria-label="Team member working at a computer in warm light" style="background:linear-gradient(135deg,#3a2a1f,#c9783a)"></div>
    <div class="body"><div class="date">JAN 24, 2022</div><h4>Sed ut perspiciatis unde omnis iste natus error sit voluptatem</h4><p>Lorem ipsum dolor sit amet consectetur adipiscing elit, sed do eiusmod tempor</p></div>
    <a class="btn btn-small" style="left:34px;top:307px;width:110px">Learn more</a>
  </article>
</section>

<section class="cta">
  <div class="abs wordmark" style="top:84px;width:100%;text-align:center;font-size:26px;color:#fff">velora</div>
  <h2>Sed ut perspiciatis unde omnis iste</h2>
  <h3>Natus error sit voluptatem</h3>
  <a class="btn btn-dark" style="left:503px;top:230px;width:166px">Contact us</a>
</section>

<footer class="site-footer">
  <div class="abs wordmark">velora</div>
  <p class="abs" style="left:152px;top:126px;width:230px;font-size:10px;line-height:15px">Lorem ipsum dolor sit amet, consectetur adipiscing elit, sed do eiusmod tempor incididunt ut labore et dolore</p>
  <p class="abs" style="left:152px;top:189px;font-size:10px;font-weight:700;color:#fff">© 2022 velora &nbsp;| All Rights Reserved</p>
  <div class="footer-col" style="left:436px"><h5>Navigation</h5>
    <ul><li>About Us</li><li>Products</li><li>Services</li><li>Contact Us</li></ul></div>
  <div class="footer-col" style="left:669px"><h5>Resources</h5>
    <ul><li>News</li><li>Team</li><li>Privacy Policy</li></ul></div>
  <div class="footer-col" style="left:895px"><h5>Follow us</h5>
    <div class="social" aria-label="Social channels"><span></span><span></span><span></span><span></span></div></div>
</footer>

</body>
</html>
```